Website Needs Designing / Populating

We are a Business Consultancy in London. We are Headhunters and Recruitment. I have bought the Domain, and Wordpress Site, installed a template from Brindle Orchard. I have tried to do it myself but do not have the time to complete or do it as I want / need.
I have some 'stock' pics and a logo - see uploaded logo files.
I want an easy to use Website - tells clients and viewers what we are about.
We are a recruitment / Headhunting Consultancy so some visitors may want to apply for positions through loading their CV / Details through the site.
We want to be about friendly but expertise. Honest and trustworthy with a heavy emphasis on Consultancy!

Target Market(s)

IT and Finance Job Seekers. Our clients are in the Marketing Communications sectors so needs to be appealing to that market

Industry/Entity Type

Business Consultant

Number of Pages Required

3 page

Requirements
Must have
• Our Logo as a central theme - see uploaded files
Nice to have
• Simple. Easy to use, inviting

```html
<!DOCTYPE html>
<html lang="en">
<head>
<meta charset="utf-8">
<title>Ledgerline Talent — Business Consultancy in London</title>
<link href="https://fonts.googleapis.com/css2?family=Raleway:wght@400;500;600;700&family=Open+Sans:wght@400;600;700&display=swap" rel="stylesheet">
<style>
:root{
  --ink:#2b2b33;
  --text:#555a60;
  --muted:#8a8f95;
  --blue:#1a93d8;
  --teal:#3bb8a9;
  --purple:#6c3590;
  --yellow:#e8b80e;
  --dark:#2a2a36;
  --grey-band:#e8e8e8;
  --white:#ffffff;
}
*{box-sizing:border-box;margin:0;padding:0}
html,body{width:1200px;height:3015px;overflow:hidden;background:var(--white)}
body{font-family:"Open Sans",Arial,sans-serif;color:var(--text);position:relative}
.heading{font-family:"Raleway",Arial,sans-serif;font-weight:400;color:var(--ink)}
section,header,footer{position:absolute;left:0;width:1200px}

/* header */
.site-header{top:0;height:78px;background:var(--white)}
.brand{position:absolute;left:98px;top:14px;display:flex;align-items:center;gap:10px}
.brand-mark{width:14px;height:14px;background:var(--blue)}
.brand-name{font-family:"Raleway",sans-serif;font-weight:600;font-size:28px;color:var(--ink);letter-spacing:.5px}
.main-nav{position:absolute;right:100px;top:34px;display:flex;gap:0}
.main-nav a{font-size:12px;color:var(--ink);text-decoration:none;text-transform:uppercase;margin-left:73px;font-weight:400}

/* hero */
.hero{top:78px;height:512px}
.hero-photo{position:absolute;inset:0;background:linear-gradient(180deg,#1d2f55 0%,#3a5788 38%,#2b3a52 62%,#4a4030 78%,#15202c 100%)}
.hero-copy{position:absolute;left:710px;top:180px;color:var(--white)}
.hero-title{font-family:"Raleway",sans-serif;font-weight:700;font-size:31px;line-height:36px;letter-spacing:.5px}
.hero-sub{font-family:"Raleway",sans-serif;font-weight:700;font-size:21px;margin-top:4px;letter-spacing:.3px}
.btn{display:inline-block;background:var(--blue);color:var(--white);font-size:12px;font-weight:700;text-transform:uppercase;border-radius:22px;text-align:center;text-decoration:none}
.hero .btn{position:absolute;left:-2px;top:88px;width:168px;height:40px;line-height:40px}

/* welcome */
.welcome{top:590px;height:528px;text-align:center}
.welcome h1{position:absolute;top:58px;width:100%;font-size:30px}
.lead{font-size:12.5px;line-height:24px;color:var(--text)}
.welcome .lead{position:absolute;top:108px;left:270px;width:660px}
.services{position:absolute;top:214px;left:98px;width:1004px;display:flex;justify-content:space-between}
.service{width:300px;text-align:center}
.service-icon{width:84px;height:84px;border-radius:50%;margin:0 auto;display:flex;align-items:center;justify-content:center}
.service-icon.teal{background:var(--teal)}
.service-icon.purple{background:var(--purple)}
.service-icon.yellow{background:var(--yellow)}
.service h3{font-family:"Raleway",sans-serif;font-weight:600;font-size:16px;color:var(--ink);margin-top:24px}
.service p{font-size:11.5px;line-height:22.5px;margin-top:12px}

/* about */
.about{top:1118px;height:362px;background:var(--dark)}
.about-photo{position:absolute;left:0;top:0;width:600px;height:362px;background:linear-gradient(135deg,#c9d4dc 0%,#8a98a4 40%,#4a4f58 75%,#2e323a 100%)}
.about-copy{position:absolute;right:94px;top:84px;width:440px;text-align:right;color:var(--white)}
.about-copy h2{font-family:"Raleway",sans-serif;font-weight:400;font-size:28px;line-height:38px;color:var(--white)}
.about-copy p{font-size:11px;line-height:22px;color:#9a9ca6;margin-top:12px}

/* posts */
.posts{top:1480px;height:730px}
.posts h2{position:absolute;top:58px;width:100%;text-align:center;font-size:29px}
.posts .lead{position:absolute;top:108px;width:100%;text-align:center}
.post-grid{position:absolute;top:172px;left:98px;width:1004px;display:flex;justify-content:space-between}
.post{width:310px}
.post-photo{height:210px}
.post-photo.one{background:linear-gradient(135deg,#dfe8ee,#6f7f90 60%,#2e3644)}
.post-photo.two{background:linear-gradient(135deg,#a8835a,#6b5a48 50%,#3a3b3e)}
.post-photo.three{background:linear-gradient(135deg,#3a88b0,#5fa2c4 50%,#2f6d90)}
.post h3{font-family:"Open Sans",sans-serif;font-weight:600;font-size:13px;line-height:25px;color:var(--ink);text-transform:uppercase;margin-top:28px}
.post .rule{width:40px;height:3px;background:var(--blue);margin-top:12px}
.post p{font-size:12.5px;line-height:25px;margin-top:16px}
.posts .btn{position:absolute;top:622px;left:518px;width:162px;height:40px;line-height:40px}

/* testimonials */
.testimonials{top:2210px;height:400px;background:var(--grey-band)}
.testimonials h2{position:absolute;top:60px;width:100%;text-align:center;font-size:29px}
.quotes{position:absolute;top:140px;left:98px;width:1004px;display:flex;justify-content:space-between}
.quote{width:300px;position:relative}
.quote blockquote{font-size:11.5px;line-height:22.5px;padding:0 20px 0 18px;position:relative}
.quote blockquote::before,.quote blockquote::after{font-family:Georgia,serif;font-size:34px;color:#b8b8b8;position:absolute}
.quote blockquote::before{content:"\201C";left:0;top:-4px}
.quote blockquote::after{content:"\201D";right:0;bottom:-28px}
.author{display:flex;align-items:center;margin-top:26px;padding-left:26px}
.avatar{width:64px;height:64px;border-radius:50%;background:linear-gradient(135deg,#c9a98c,#7d6452);border:3px solid var(--white)}
.author-name{margin-left:22px}
.author-name strong{display:block;font-family:"Raleway",sans-serif;font-weight:600;font-size:14px;color:var(--ink)}
.author-name span{font-size:11px;color:var(--muted)}

/* partners */
.partners{top:2610px;height:110px;display:flex;align-items:center;justify-content:space-between;padding:0 100px}
.partner{display:flex;align-items:center;gap:8px;font-family:"Open Sans",sans-serif;font-weight:600;font-size:15px;color:#9a9da2}
.partner i{width:12px;height:12px;border-radius:50%;background:#b9bcc0;display:block}

/* footer */
.site-footer{top:2720px;height:295px;background:var(--dark);text-align:center}
.site-footer .brand{position:absolute;left:0;right:0;top:52px;justify-content:center}
.site-footer .brand-name{color:var(--white)}
.footer-nav{position:absolute;top:122px;width:100%;display:flex;justify-content:center;gap:60px}
.footer-nav a{font-size:11.5px;color:#c4c5cc;text-decoration:none}
.copyright{position:absolute;top:152px;width:100%;font-size:11px;color:#a5a7b0}
.social{position:absolute;top:196px;width:100%;display:flex;justify-content:center;gap:16px}
.social span{width:28px;height:28px;border-radius:50%;background:#4a4a57;display:block}
</style>
</head>
<body>

<header class="site-header">
  <div class="brand"><span class="brand-mark"></span><span class="brand-name">Ledgerline Talent</span></div>
  <nav class="main-nav">
    <a href="#">Home</a><a href="#">About Us</a><a href="#">Services</a><a href="#">Blog</a><a href="#">Testimonials</a><a href="#">Contact Us</a>
  </nav>
</header>

<section class="hero">
  <div class="hero-photo" role="img" aria-label="Evening photograph of a London river bridge lit up against a blue sky"></div>
  <div class="hero-copy">
    <div class="hero-title">WE ARE A</div>
    <div class="hero-sub">BUSINESS CONSULTANCY IN LONDON</div>
    <a class="btn" href="#">Get in touch!</a>
  </div>
</section>

<section class="welcome">
  <h1 class="heading">Welcome to Ledgerline Talent</h1>
  <p class="lead">Lorem Ipsum is simply dummy text of the printing and typesetting industry. Lorem Ipsum has been the industry's standard dummy text ever since the 1500s</p>
  <div class="services">
    <div class="service">
      <div class="service-icon teal">
        <svg width="40" height="30" viewBox="0 0 40 30" fill="none" stroke="#fff" stroke-width="2.2" stroke-linecap="round" stroke-linejoin="round"><path d="M2 10l8-6 8 4 6-3 14 6"/><path d="M10 4l-4 14 10 8 8-6 10 2"/><path d="M18 8l-6 6 4 3 8-5"/></svg>
      </div>
      <h3>Consulting</h3>
      <p>Lorem Ipsum is simply dummy text of the printing and typesetting industry. Lorem Ipsum has been the industry's standard dummy text ever since the 1500s, when an unknown printer...</p>
    </div>
    <div class="service">
      <div class="service-icon purple">
        <svg width="34" height="34" viewBox="0 0 34 34" fill="none" stroke="#fff" stroke-width="2.2"><circle cx="17" cy="11" r="7"/><path d="M4 32c0-8 6-12 13-12s13 4 13 12z"/></svg>
      </div>
      <h3>Headhunters</h3>
      <p>Lorem Ipsum is simply dummy text of the printing and typesetting industry. Lorem Ipsum has been the industry's standard dummy text ever since the 1500s, when an unknown printer...</p>
    </div>
    <div class="service">
      <div class="service-icon yellow">
        <svg width="36" height="36" viewBox="0 0 36 36" fill="none" stroke="#fff" stroke-width="2.4" stroke-linecap="round"><circle cx="15" cy="15" r="10"/><path d="M22.5 22.5L33 33"/></svg>
      </div>
      <h3>Recruitment</h3>
      <p>Lorem Ipsum is simply dummy text of the printing and typesetting industry. Lorem Ipsum has been the industry's standard dummy text ever since the 1500s, when an unknown printer...</p>
    </div>
  </div>
</section>

<section class="about">
  <div class="about-photo" role="img" aria-label="Photograph of a team meeting around a boardroom table with laptops"></div>
  <div class="about-copy">
    <h2>About<br>Ledgerline Talent</h2>
    <p>Lorem Ipsum is simply dummy text of the printing and typesetting industry. Lorem Ipsum has been the industry's standard dummy text ever since the 1500s, when an unknown printer took a galley of type and scrambled it to make a type specimen book. It has survived not only five centuries...</p>
  </div>
</section>

<section class="posts">
  <h2 class="heading">Recent Posts</h2>
  <p class="lead">Lorem Ipsum is simply dummy text of the printing and typesetting industry. Lorem Ipsum has been the industry...</p>
  <div class="post-grid">
    <article class="post">
      <div class="post-photo one" role="img" aria-label="Photograph of two business colleagues reviewing documents"></div>
      <h3>Lorem Ipsum is simply dummy text<br>of the printing</h3>
      <div class="rule"></div>
      <p>Lorem Ipsum is simply dummy text of the printing and typesetting industry. Lorem Ipsum has been the industry's standard dummy text ever since the 1500s.</p>
    </article>
    <article class="post">
      <div class="post-photo two" role="img" aria-label="Overhead photograph of a group working around a table with laptops"></div>
      <h3>Lorem Ipsum is simply dummy text<br>of the printing</h3>
      <div class="rule"></div>
      <p>Lorem Ipsum is simply dummy text of the printing and typesetting industry. Lorem Ipsum has been the industry's standard dummy text ever since the 1500s.</p>
    </article>
    <article class="post">
      <div class="post-photo three" role="img" aria-label="Photograph of a job seeker holding up a printed CV"></div>
      <h3>Lorem Ipsum is simply dummy text<br>of the printing</h3>
      <div class="rule"></div>
      <p>Lorem Ipsum is simply dummy text of the printing and typesetting industry. Lorem Ipsum has been the industry's standard dummy text ever since the 1500s.</p>
    </article>
  </div>
  <a class="btn" href="#">View more</a>
</section>

<section class="testimonials">
  <h2 class="heading">What our client's say</h2>
  <div class="quotes">
    <figure class="quote">
      <blockquote>Lorem Ipsum is simply dummy text of the printing and typesetting industry. Lorem Ipsum has been the industry's standard dummy text ever since the</blockquote>
      <figcaption class="author"><div class="avatar" role="img" aria-label="Client portrait"></div><div class="author-name"><strong>Miles Harcourt</strong><span>Business man</span></div></figcaption>
    </figure>
    <figure class="quote">
      <blockquote>Lorem Ipsum is simply dummy text of the printing and typesetting industry. Lorem Ipsum has been the industry's standard dummy text ever since the</blockquote>
      <figcaption class="author"><div class="avatar" role="img" aria-label="Client portrait"></div><div class="author-name"><strong>Miles Harcourt</strong><span>Business man</span></div></figcaption>
    </figure>
    <figure class="quote">
      <blockquote>Lorem Ipsum is simply dummy text of the printing and typesetting industry. Lorem Ipsum has been the industry's standard dummy text ever since the</blockquote>
      <figcaption class="author"><div class="avatar" role="img" aria-label="Client portrait"></div><div class="author-name"><strong>Miles Harcourt</strong><span>Business man</span></div></figcaption>
    </figure>
  </div>
</section>

<section class="partners">
  <div class="partner"><i></i>Corvane</div>
  <div class="partner">Halden Works</div>
  <div class="partner"><i></i>Petrova</div>
  <div class="partner">Tindale</div>
  <div class="partner">Marrow Lane</div>
  <div class="partner"><i></i>Fenwick Labs</div>
  <div class="partner">Ostrey Group</div>
</section>

<footer class="site-footer">
  <div class="brand"><span class="brand-mark"></span><span class="brand-name">Ledgerline Talent</span></div>
  <nav class="footer-nav"><a href="#">Home</a><a href="#">About Us</a><a href="#">Services</a><a href="#">Blog</a><a href="#">Testimonials</a><a href="#">Contact us</a></nav>
  <p class="copyright">Ledgerline Talent, 2016. All Rights Reserved</p>
  <div class="social" aria-label="Social links"><span></span><span></span><span></span><span></span><span></span><span></span></div>
</footer>

</body>
</html>
```